BOLD & MINIMALIST DESIGN NEEDED

We want a very bold but minimalistic business card design that is impactful and utilizes both sides of the business card. Our current logo is included for your use.

We want bold fonts and good use of negative space. We don't want the logo to overpower the design.

Target Market(s)

Professionals who are building new commercial buildings.

Industry/Entity Type

Construction

Contact Information for Business Card

Name, Title, email, office phone, cell phone, website

Font styles to use
Serif
Sans Serif

Requirements
Must have
• Bold design!

```html
<!DOCTYPE html>
<html lang="en">
<head>
<meta charset="UTF-8">
<title>Summitline Design + Build – Business Card</title>
<link rel="stylesheet" href="https://fonts.googleapis.com/css2?family=Montserrat:wght@400;500;800&display=swap">
<style>
  :root {
    --lime: #84c441;
    --lime-light: #9bd158;
    --forest: #3f7a1f;
    --ink: #161616;
    --paper: #ffffff;
    --ghost: #eef0ee;
    --stage: #e4e6e3;
    --text: #2a2a2a;
  }
  * { box-sizing: border-box; margin: 0; padding: 0; }
  html, body {
    width: 1200px; height: 874px; overflow: hidden;
    background: var(--stage);
    font-family: "Montserrat", Arial, sans-serif;
  }
  .canvas {
    width: 1200px; height: 874px;
    display: flex; flex-direction: column; align-items: center; justify-content: center;
    gap: 56px;
  }
  .card {
    width: 620px; height: 354px;
    border-radius: 22px;
    position: relative; overflow: hidden;
    box-shadow: 0 10px 30px rgba(0,0,0,.18);
  }
  /* Front */
  .card-front {
    background: linear-gradient(135deg, var(--lime) 0%, var(--lime-light) 100%);
    display: flex; align-items: center; justify-content: center; gap: 16px;
  }
  .front-mark {
    width: 34px; height: 34px; background: var(--forest);
  }
  .front-name {
    font-weight: 800; font-size: 44px; letter-spacing: 1px;
    color: var(--forest); text-transform: uppercase; line-height: 1.1;
    text-align: left;
  }
  /* Back */
  .card-back { background: var(--paper); }
  .brand {
    position: absolute; left: 40px; top: 40px;
    display: flex; align-items: center; gap: 10px;
  }
  .brand-mark { width: 22px; height: 22px; background: var(--lime); }
  .brand-name {
    font-weight: 800; font-size: 26px; color: var(--ink);
    text-transform: uppercase; letter-spacing: .5px; line-height: 1.1;
  }
  .address {
    position: absolute; left: 40px; top: 112px;
    font-size: 15px; font-weight: 500; color: var(--text); line-height: 1.35;
  }
  .contact-list {
    position: absolute; left: 40px; top: 178px;
    list-style: none; font-size: 15px; font-weight: 500; color: var(--text);
  }
  .contact-list li { display: flex; align-items: center; gap: 10px; height: 26px; }
  .contact-list svg { width: 14px; height: 14px; fill: var(--lime); flex: none; }
  .ghost-block {
    position: absolute; right: 60px; top: 150px;
    width: 190px; height: 180px; background: var(--ghost);
  }
  .holder {
    position: absolute; right: 46px; top: 206px; text-align: right;
  }
  .holder-name {
    font-weight: 800; font-size: 30px; color: var(--lime);
    text-transform: uppercase; letter-spacing: .5px;
  }
  .holder-title {
    font-weight: 500; font-size: 16px; color: var(--text); letter-spacing: .5px;
    margin-top: 2px;
  }
  .edge-bar {
    position: absolute; right: 20px; top: 210px;
    width: 14px; height: 62px; background: var(--lime);
  }
</style>
</head>
<body>
<main class="canvas">
  <section class="card card-front" aria-label="Card front">
    <span class="front-mark"></span>
    <h1 class="front-name">Summitline<br>Design + Build</h1>
  </section>

  <section class="card card-back" aria-label="Card back">
    <div class="brand">
      <span class="brand-mark"></span>
      <span class="brand-name">Summitline<br>Design + Build</span>
    </div>
    <p class="address">48 Ridgeway Ave, Dover<br>State, Zip 5821</p>
    <ul class="contact-list">
      <li><svg viewBox="0 0 24 24"><path d="M6.6 10.8a15 15 0 0 0 6.6 6.6l2.2-2.2c.3-.3.7-.4 1-.2 1.1.4 2.3.6 3.6.6.6 0 1 .4 1 1V20c0 .6-.4 1-1 1A17 17 0 0 1 3 4c0-.6.4-1 1-1h3.5c.6 0 1 .4 1 1 0 1.3.2 2.5.6 3.6.1.3 0 .7-.2 1z"/></svg>555 204 318</li>
      <li><svg viewBox="0 0 24 24"><path d="M7 1h10a2 2 0 0 1 2 2v18a2 2 0 0 1-2 2H7a2 2 0 0 1-2-2V3a2 2 0 0 1 2-2zm0 3v14h10V4zm5 15.5a1 1 0 1 0 0 2 1 1 0 0 0 0-2z"/></svg>555 730 462</li>
      <li><svg viewBox="0 0 24 24"><path d="M2 5h20v14H2zm2 2v.4l8 5 8-5V7zm0 2.8V17h16V9.8l-8 5z"/></svg>info@summitline.com</li>
      <li><svg viewBox="0 0 24 24"><path d="M12 2a10 10 0 1 0 0 20 10 10 0 0 0 0-20zm6.9 9h-3a15 15 0 0 0-1.3-5.6A8 8 0 0 1 18.9 11zM12 4c.9 1.2 1.8 3.7 1.9 7h-3.8c.1-3.3 1-5.8 1.9-7zM9.4 5.4A15 15 0 0 0 8.1 11h-3a8 8 0 0 1 4.3-5.6zM5.1 13h3a15 15 0 0 0 1.3 5.6A8 8 0 0 1 5.1 13zm6.9 7c-.9-1.2-1.8-3.7-1.9-7h3.8c-.1 3.3-1 5.8-1.9 7zm2.6-1.4a15 15 0 0 0 1.3-5.6h3a8 8 0 0 1-4.3 5.6z"/></svg>www.summitline.com</li>
    </ul>
    <div class="ghost-block"></div>
    <div class="holder">
      <p class="holder-name">Ravi Mehta</p>
      <p class="holder-title">OWNER-CEO</p>
    </div>
    <span class="edge-bar"></span>
  </section>
</main>
</body>
</html>
```